Bramwell Corner Sports Pub. Where the locals go!!

We are creating a sports pub. We are needing a fun website that offers our menu along with an event page and general info. We have some attached links that we really like:
https://www.dunmorrows.example/
https://www.cafepelindra.example/
https://www.quillstoneyx.example/
We are doing a pirate theme but that is because the area we are in. We would like to see a pirate like in our logo doing something like drinking real time similar to the dunmorrows website above.
Target Market(s)
Sports Fans
Industry/Entity Type
Pub, Bar, Restaurant
Coding
Coded - Design and coding required
Number of Pages Required
3 page
Font styles to use
Other font styles liked:
- see uploads
Look and feel

```html
<!DOCTYPE html>
<html lang="en">
<head>
<meta charset="utf-8">
<title>Bramwell Corner Sports Pub</title>
<link rel="stylesheet" href="https://fonts.googleapis.com/css2?family=Bebas+Neue&family=Poppins:wght@400;500&display=swap">
<style>
:root{
  --ink:#2a2623;
  --night:#1f1d1b;
  --brown:#7a4d22;
  --brown-deep:#5c3a1b;
  --bronze:#8a5a2b;
  --cream:#f3dfb5;
  --paper:#dcb879;
  --fog:#e9e8ee;
  --white:#ffffff;
  --head:'Bebas Neue',sans-serif;
  --body:'Poppins',sans-serif;
}
*{margin:0;padding:0;box-sizing:border-box}
html,body{width:1200px;height:3856px;overflow:hidden}
body{position:relative;font-family:var(--body);color:var(--ink);background:var(--night)}
section,header,footer{position:absolute;left:0;width:1200px;overflow:hidden}
.abs{position:absolute}
.head{font-family:var(--head);font-weight:400;letter-spacing:.5px;line-height:1}

/* hero */
.hero{top:0;height:600px;background:radial-gradient(ellipse at 50% 30%,#5a5048 0%,#3a2f28 45%,#1d1815 100%)}
.hero .photo{position:absolute;inset:0}
.navbar{top:0;left:0;width:1200px;height:96px;background:rgba(30,30,30,.55)}
.brand{left:160px;top:28px;color:var(--white);font-family:var(--head);font-size:20px;line-height:20px;display:flex;align-items:center;gap:10px}
.brand .dot{flex:none;width:18px;height:18px;border-radius:50%;background:var(--bronze)}
.nav{top:46px;font-family:var(--head);font-size:22px;color:var(--white)}
.nav span{position:absolute;white-space:nowrap}
.hero h1{position:absolute;top:205px;width:1200px;text-align:center;color:var(--white);font-size:80px;line-height:76px}
.btn-light{position:absolute;left:504px;top:395px;width:183px;height:54px;border-radius:12px;background:var(--white);color:var(--ink);font-family:var(--head);font-size:23px;display:flex;align-items:center;justify-content:center}

/* about */
.about{top:600px;height:606px;background:linear-gradient(180deg,#eeeef2,#dcdde3)}
.ring{position:absolute;border-radius:50%}
.about h2{left:610px;top:120px;font-size:50px;color:var(--brown)}
.about p{left:610px;top:180px;width:480px;font-size:16px;line-height:30px;color:#4a4540;text-align:justify}
.btn-brown{left:597px;top:439px;width:174px;height:55px;border-radius:16px;background:var(--brown);color:var(--white);font-family:var(--head);font-size:23px;display:flex;align-items:center;justify-content:center}

/* menus */
.menus{top:1206px;height:840px;background:linear-gradient(180deg,#7b4e22,#6a4320)}
.menus h2{top:98px;width:1200px;text-align:center;color:var(--white);font-size:50px}
.tab{top:168px;width:208px;height:56px;border-radius:14px;background:var(--white);color:var(--ink);font-family:var(--head);font-size:23px;display:flex;align-items:center;justify-content:center}
.tab.active{background:var(--ink);color:var(--white)}
.scroll{left:136px;top:255px;width:385px;height:473px;border-radius:18px;background:linear-gradient(90deg,#c9a064,#e6c386 50%,#c9a064)}
.scroll-text{left:136px;top:318px;width:385px;text-align:center;color:var(--white)}
.scroll-text .title{font-size:50px}
.scroll-text .note{font-size:21px;margin-top:6px}
.scroll-text ul{list-style:none;margin-top:20px;font-size:20px;line-height:32.5px}
.dish-photo{left:611px;top:265px;width:477px;height:210px;border-radius:10px;background:linear-gradient(135deg,#6b4a2e,#d9a24a 45%,#e9c06a 60%,#5a3a22)}
.dish-name{left:629px;top:506px;font-size:50px;color:var(--white)}
.dish-price{left:950px;top:502px;font-size:52px;color:var(--white)}
.dish-desc{left:629px;top:560px;width:436px;font-size:16px;line-height:30px;color:var(--white)}

/* events */
.events{top:2046px;height:786px;background:#272523}
.events h2{top:96px;width:1200px;text-align:center;color:var(--white);font-size:50px}
.parchment{left:221px;top:159px;width:752px;height:522px;background:linear-gradient(135deg,#c99c60,#e7c993 40%,#d9b57a 70%,#b88a52)}
.date{left:316px;width:123px;height:117px;border-radius:12px;background:var(--white);text-align:center;font-family:var(--head);font-size:46px;line-height:40px;color:var(--ink);padding-top:16px}
.event-title{left:458px;font-size:48px;color:var(--brown-deep)}
.event-sub{left:467px;font-size:17px;color:#9a6a35}
.see-more{font-size:20px;display:flex;align-items:center;gap:12px}
.see-more span{border-bottom:1.5px solid currentColor;line-height:24px}

/* testimonials */
.testimonials{top:2832px;height:613px;background:linear-gradient(180deg,#f0d8a6,#f6e4bd)}
.testimonials h2{top:118px;width:1200px;text-align:center;color:#4a2c17;font-size:50px}
.quote{left:359px;top:295px;width:460px;height:193px;border-radius:26px;background:var(--brown)}
.quote-tip{left:575px;top:486px}
.avatar{left:517px;top:221px;width:140px;height:140px;border-radius:50%;border:6px solid var(--white);background:linear-gradient(160deg,#d9b08c,#a77a5a)}
.author{left:417px;top:330px;font-size:15px;color:#f3e6d2}
.stars{left:688px;top:326px;font-size:18px;color:#f4c430;letter-spacing:1px}
.quote p{position:absolute;left:50px;top:70px;width:358px;font-size:15px;line-height:30px;color:#f3e6d2;text-align:justify}

/* footer */
footer{top:3445px;height:411px;background:linear-gradient(180deg,#2b2622,#221e1b)}
.foot-brand{top:168px;width:1200px;text-align:center;color:var(--white);font-size:24px}
.foot-brand .dot{display:inline-block;width:18px;height:18px;border-radius:50%;background:var(--bronze);vertical-align:-2px;margin-right:10px}
.foot-nav{top:217px;font-family:var(--head);font-size:22px;color:var(--white)}
.foot-nav span{position:absolute;white-space:nowrap}
.social{top:271px;left:499px;display:flex;gap:30px}
.social i{display:block;width:16px;height:16px;border-radius:50%;background:var(--white)}
.copyright{top:312px;left:0;width:1200px;height:99px;background:#1b1918;color:var(--white);font-size:15px;text-align:center;padding-top:26px}
</style>
</head>
<body>

<header class="hero">
  <div class="photo" role="img" aria-label="Sports fans cheering with drinks in a dim pub facing a big match screen"></div>
  <div class="abs navbar"></div>
  <div class="abs brand"><span class="dot"></span><span>Bramwell Corner<br>Sports Pub</span></div>
  <nav class="abs nav" style="left:0;top:46px">
    <span style="left:364px">Home</span>
    <span style="left:462px">About Us</span>
    <span style="left:589px">Our Menus</span>
    <span style="left:728px">Events</span>
    <span style="left:843px">Testimonials</span>
    <span style="left:1006px">Contact Us</span>
  </nav>
  <h1 class="head">Welcome to<br>Bramwell Corner Sports Pub</h1>
  <a class="btn-light">Get Started</a>
</header>

<section class="about">
  <div class="ring" style="left:95px;top:64px;width:424px;height:424px;background:var(--brown)"></div>
  <div class="ring" role="img" aria-label="Group of friends cheering in a pub" style="left:113px;top:82px;width:388px;height:388px;background:linear-gradient(135deg,#5a4535,#b07a4a 50%,#3b2e26)"></div>
  <div class="ring" style="left:317px;top:81px;width:234px;height:234px;background:var(--white)"></div>
  <div class="ring" role="img" aria-label="Fans in a stadium raising beers" style="left:328px;top:92px;width:212px;height:212px;background:linear-gradient(180deg,#6b9a4a,#4f7a3a 40%,#7a5a48)"></div>
  <h2 class="abs head">About Us</h2>
  <p class="abs">Lorem ipsum dolor sit amet, consectetur adipiscing elit, sed do eiusmod tempor incididunt ut labore et dolore magna aliqua. Ut enim ad minim veniam, quis nostrud exercitation ullamco laboris nisi ut aliquip ex ea commodo consequat. Duis aute irure dolor in reprehenderit in voluptate velit esse cillum dolore eu fugiat nulla pariatur. Excepteur sint occaecat cupidatat non proident, sunt in culpa qui officia deserunt mollit anim id est laborum</p>
  <a class="abs btn-brown">Reed More</a>
</section>

<section class="menus">
  <h2 class="abs head">Our Menus</h2>
  <div class="abs tab active" style="left:248px">Main Menu</div>
  <div class="abs tab" style="left:471px">Daily Specials</div>
  <div class="abs tab" style="left:694px">Wine</div>
  <div class="abs scroll" role="img" aria-label="Parchment scroll"></div>
  <div class="abs scroll-text head">
    <div class="title">Main Menu</div>
    <div class="note" style="color:var(--ink)">All appetizers include sauce</div>
    <ul>
      <li>Cheese Curds</li><li>$10.00</li>
      <li>Pepperjack Cubes</li><li>$10.00</li>
      <li style="color:var(--ink)">Cheese Curds</li><li>$10.00</li>
      <li>Pepperjack Cubes</li><li>$10.00</li>
    </ul>
  </div>
  <div class="abs dish-photo" role="img" aria-label="Fried cheese curds with dipping sauce"></div>
  <div class="abs head dish-name">Cheese Curds</div>
  <div class="abs head dish-price">$10.00</div>
  <p class="abs dish-desc">Lorem ipsum dolor sit amet, consectetur adipiscing elit, sed do eiusmod tempor incididunt ut labore et dolore magna aliqua. Ut enim ad minim veniam, quis nostrud exercitation ullamco laboris nisi ut aliquip ex ea commodo consequat. Duis aute</p>
</section>

<section class="events">
  <h2 class="abs head">Events</h2>
  <div class="abs parchment" role="img" aria-label="Torn old treasure map parchment"></div>
  <div class="abs date" style="top:202px">July<br>21</div>
  <div class="abs head event-title" style="top:226px">Sed ut perspiciatis unde</div>
  <div class="abs event-sub" style="top:276px">omnis iste natus error sit voluptatem</div>
  <div class="abs date" style="top:349px">July<br>24</div>
  <div class="abs head event-title" style="top:372px">Sed ut perspiciatis unde</div>
  <div class="abs event-sub" style="top:422px">omnis iste natus error sit voluptatem</div>
  <div class="abs date" style="top:497px">July<br>28</div>
  <div class="abs head event-title" style="top:521px">Sed ut perspiciatis unde</div>
  <div class="abs event-sub" style="top:571px">omnis iste natus error sit voluptatem</div>
  <div class="abs see-more" style="left:787px;top:624px;color:#4a2c17">
    <span>SEE MORE</span>
    <svg width="28" height="14" viewBox="0 0 28 14"><path d="M1 7h24M19 1l6 6-6 6" fill="none" stroke="#4a2c17" stroke-width="2.5"/></svg>
  </div>
</section>

<section class="testimonials">
  <h2 class="abs head">Testimonials</h2>
  <div class="abs quote">
    <p>Sed ut perspiciatis unde omnis iste natus error sit voluptatem accusantium doloremque laudantium, totam rem aperiam, eaque ipsa</p>
  </div>
  <svg class="abs quote-tip" width="34" height="26" viewBox="0 0 34 26"><path d="M0 0h34L17 26z" fill="#7a4d22"/></svg>
  <div class="abs avatar" role="img" aria-label="Customer portrait"></div>
  <div class="abs author">– TOBIN</div>
  <div class="abs stars">★★★★★</div>
  <div class="abs see-more" style="left:847px;top:462px;color:#2a2623">
    <span>SEE MORE</span>
    <svg width="28" height="14" viewBox="0 0 28 14"><path d="M1 7h24M19 1l6 6-6 6" fill="none" stroke="#2a2623" stroke-width="2.5"/></svg>
  </div>
</section>

<footer>
  <div class="abs head foot-brand"><span class="dot"></span>Bramwell Corner Sports Pub</div>
  <nav class="abs foot-nav" style="left:0">
    <span style="left:225px">Home</span>
    <span style="left:325px">About Us</span>
    <span style="left:450px">Our Menus</span>
    <span style="left:590px">Events</span>
    <span style="left:705px">Testimonials</span>
    <span style="left:868px">Contact Us</span>
  </nav>
  <div class="abs social" aria-label="Social links"><i></i><i></i><i></i><i></i><i></i></div>
  <div class="abs copyright">© 2023 Bramwell Corner Sports Pub</div>
</footer>

</body>
</html>
```